Oil Field Service company needs professional business cards

Looking to clean up our current company business cards and look a little more professional. Brenwick Casing Services is a US based company that services the oil field. We deal with engineers, managers and oil rigs....................................................................................................................................................................................................................................................................................................................................................................................................

Target Market(s)

Oil and Gas professionals

Industry/Entity Type

Oil And Gas

Contact Information for Business Card

See attached photo as example

Font styles to use
Sans Serif

Colors
ec1f27

Requirements
Must have
• Company Logo, Name, Title, Cell, Office, Fax, Email.
• See attached photo
Nice to have
• External CRT, Internal CRT, Casing Crews, Torque Turn, Laydown Machine
Should not have
• Do not introduce any new pictures and keep it professional looking

```html
<!DOCTYPE html>
<html lang="en">
<head>
<meta charset="utf-8">
<title>Brenwick Casing Services – Business Cards</title>
<link href="https://fonts.googleapis.com/css2?family=Open+Sans:wght@400;600;700;800&display=swap" rel="stylesheet">
<style>
  :root {
    --red: #ec1f27;
    --slate: #3f4d5a;
    --ink: #3a3f45;
    --grey: #5b6169;
    --white: #ffffff;
    --backdrop: #e9e7e4;
  }
  * { box-sizing: border-box; margin: 0; padding: 0; }
  html, body {
    width: 1200px; height: 950px; overflow: hidden;
    background: var(--backdrop);
    font-family: "Open Sans", Arial, sans-serif;
  }
  .sheet {
    width: 1200px; height: 950px;
    display: flex; flex-direction: column; align-items: center; justify-content: center;
    gap: 50px;
  }
  .card {
    position: relative;
    width: 700px; height: 400px;
    border-radius: 4px;
    overflow: hidden;
    box-shadow: 0 6px 18px rgba(0,0,0,.18);
  }

  /* Front */
  .card--front { background: var(--white); }
  .front__band-top {
    position: absolute; left: 0; right: 0; top: 34px; height: 34px;
    background: var(--red);
  }
  .front__band-bottom {
    position: absolute; left: 0; right: 0; bottom: 0; height: 40px;
    background: var(--red);
    display: flex; align-items: center; justify-content: flex-end;
    padding-right: 34px;
  }
  .front__web {
    color: var(--white); font-size: 15px; letter-spacing: 3px; font-weight: 600;
  }
  .brand { display: flex; flex-direction: column; align-items: center; }
  .brand__name {
    display: flex; align-items: center; gap: 12px;
    font-weight: 800; font-size: 54px; line-height: 1; letter-spacing: 1px;
  }
  .brand__dot { width: 16px; height: 16px; border-radius: 50%; background: var(--red); }
  .brand__tag {
    margin-top: 8px; font-weight: 700; font-size: 16px; letter-spacing: 5px;
  }
  .front .brand { position: absolute; left: 44px; top: 100px; }
  .front .brand__name { color: var(--ink); }
  .front .brand__tag { color: var(--ink); }

  .person { position: absolute; left: 44px; top: 230px; }
  .person__name { color: var(--red); font-weight: 600; font-size: 26px; }
  .person__title, .person__address { color: var(--grey); font-size: 16px; margin-top: 4px; }

  .contacts {
    position: absolute; right: 44px; top: 108px;
    list-style: none; display: flex; flex-direction: column; gap: 10px;
  }
  .contacts__item {
    display: flex; align-items: center; gap: 12px;
    color: var(--grey); font-size: 17px;
  }
  .contacts__icon { width: 18px; height: 18px; flex: none; }
  .contacts__icon path, .contacts__icon rect { fill: none; stroke: var(--red); stroke-width: 2; }
  .contacts__icon .solid { fill: var(--red); stroke: none; }

  /* Back */
  .card--back {
    background: var(--slate);
    display: flex; flex-direction: column; align-items: center; justify-content: center;
  }
  .back .brand__name { color: var(--white); font-size: 66px; }
  .back .brand__tag { color: var(--white); font-size: 19px; letter-spacing: 7px; margin-top: 12px; }
  .services {
    margin-top: 34px; text-align: center; color: var(--white);
    font-size: 17px; line-height: 1.6;
  }
</style>
</head>
<body>
<main class="sheet">

  <section class="card card--front front" aria-label="Business card front">
    <div class="front__band-top"></div>

    <div class="brand">
      <div class="brand__name"><span class="brand__dot"></span>BRENWICK</div>
      <div class="brand__tag">CASING SERVICES</div>
    </div>

    <div class="person">
      <p class="person__name">Wade Hollister</p>
      <p class="person__title">Area Manager</p>
      <p class="person__address">Alder Creek, OK 73000</p>
    </div>

    <ul class="contacts">
      <li class="contacts__item">
        <svg class="contacts__icon" viewBox="0 0 18 18" aria-label="Office"><path class="solid" d="M4 1h3l1.5 4-2 1.5a10 10 0 0 0 5 5L13 9.5l4 1.5v3a2 2 0 0 1-2 2A14 14 0 0 1 2 3a2 2 0 0 1 2-2z"/></svg>
        (555)214-3800
      </li>
      <li class="contacts__item">
        <svg class="contacts__icon" viewBox="0 0 18 18" aria-label="Cell"><rect x="4" y="1" width="10" height="16" rx="2"/></svg>
        (555)617-2093
      </li>
      <li class="contacts__item">
        <svg class="contacts__icon" viewBox="0 0 18 18" aria-label="Fax"><rect class="solid" x="2" y="7" width="14" height="8" rx="1"/><rect x="5" y="2" width="8" height="5"/></svg>
        (555)214-3811
      </li>
      <li class="contacts__item">
        <svg class="contacts__icon" viewBox="0 0 18 18" aria-label="Email"><rect x="1.5" y="3.5" width="15" height="11" rx="1"/><path d="M2 4l7 6 7-6"/></svg>
        wade@brenwick.com
      </li>
    </ul>

    <div class="front__band-bottom">
      <span class="front__web">www.brenwick.com</span>
    </div>
  </section>

  <section class="card card--back back" aria-label="Business card back">
    <div class="brand">
      <div class="brand__name"><span class="brand__dot"></span>BRENWICK</div>
      <div class="brand__tag">CASING SERVICES</div>
    </div>
    <p class="services">External CRT • Internal CRT • Casing Crews<br>Torque Turn • Laydown Machine</p>
  </section>

</main>
</body>
</html>
```